Fresh, modern, fun business card for pediatric dental practice

Need a business card for fresh, modern, fun pediatric dental practice

Clean look that matches our website's font and colors

We prefer the look of curved corners on business cards

Target Market(s)

parents (mothers) of young children, professionals, mid-high class

Industry/Entity Type

Dental

Contact Information for Business Card

Maplebrook Pediatric Dentistry
482 Quarry Lane
Suite 517
Alderwick, ST 00000
555.555.0193
www.maplebrookkidsdental.example

Mei-Ran Tsai, DMD
Corinne Walbeck, DMD
(we are working on our email address, but we would like that on the card as well)

Font styles to use
Sans Serif

Requirements
Must have
• All info; we would also like to make cards for individual staff members
• colors from our website and color palatte, attatched
• use same font and design as website for branding
Nice to have
• clean, simple card that has a pop of color
• we would like to see a few designs with our tag line "where smiles get brighter"
• we are not sure if we want to have it on there or not
• we would like to see a few designs incorporating the ribbon graphic on our website where the word WELCOME is

```html
<!DOCTYPE html>
<html lang="en">
<head>
<meta charset="utf-8">
<title>Maplebrook Pediatric Dentistry – Business Card</title>
<link rel="stylesheet" href="https://fonts.googleapis.com/css2?family=Open+Sans:wght@400;600&display=swap">
<style>
  :root {
    --magenta: #e94bf4;
    --magenta-deep: #d14bef;
    --sun: #f3b316;
    --gold: #e0a800;
    --gold-dark: #a07c00;
    --mist-top: #ffffff;
    --mist-bottom: #e8ecec;
    --slate: #c3d0cf;
    --ribbon: #b0b0aa;
    --plum: #4d2a6e;
    --violet: #7a3fa1;
    --white: #ffffff;
  }
  * { margin: 0; padding: 0; box-sizing: border-box; }
  html, body { width: 1200px; height: 720px; overflow: hidden; background: #ffffff; }
  .card {
    position: relative;
    width: 1200px; height: 720px;
    overflow: hidden;
    font-family: "Open Sans", sans-serif;
    background: linear-gradient(var(--mist-top), var(--mist-bottom) 292px);
  }
  .top-wave { position: absolute; left: 0; top: 0; width: 1200px; height: 90px; }
  .brand {
    position: absolute; left: 0; right: 0; top: 110px;
    display: flex; flex-direction: column; align-items: center; gap: 22px;
  }
  .brand-dot { width: 58px; height: 58px; border-radius: 50%; background: var(--sun); }
  .brand-name {
    color: var(--sun); font-weight: 600; font-size: 46px;
    letter-spacing: 1px; line-height: 1;
  }
  .stripe { position: absolute; left: 0; width: 1200px; height: 22px; background: var(--gold-dark); }
  .stripe--upper { top: 292px; }
  .stripe--lower { top: 555px; }
  .contact-band {
    position: absolute; left: 0; top: 314px; width: 1200px; height: 241px;
    background: var(--gold); color: var(--white);
  }
  .doctor {
    position: absolute; left: 0; right: 0; top: 38px;
    text-align: center; font-size: 38px; font-weight: 400; letter-spacing: -0.5px;
  }
  .contact-row {
    position: absolute; left: 0; right: 0;
    display: flex; justify-content: center; gap: 68px;
    font-size: 23px;
  }
  .contact-row--first { top: 123px; }
  .contact-row--second { top: 188px; }
  .contact-item { display: flex; align-items: center; gap: 14px; }
  .contact-icon { width: 30px; height: 30px; flex: none; }
  .address-band {
    position: absolute; left: 0; top: 577px; width: 1200px; height: 91px;
    background: var(--slate);
  }
  .ribbon { position: absolute; left: 310px; top: 8px; width: 610px; height: 76px; }
  .ribbon-text {
    position: absolute; left: 310px; top: 8px; width: 570px; height: 76px;
    display: flex; flex-direction: column; justify-content: center; align-items: center;
    line-height: 1.25;
  }
  .practice { color: var(--plum); font-size: 23px; font-weight: 600; letter-spacing: -0.3px; }
  .address { color: var(--violet); font-size: 23px; font-weight: 400; letter-spacing: -0.3px; }
  .bottom-band {
    position: absolute; left: 0; top: 668px; width: 1200px; height: 52px;
    background: var(--magenta);
  }
  .bottom-band-inner {
    position: absolute; left: 66px; top: 13px; right: 0; bottom: 0;
    background: var(--magenta-deep);
  }
</style>
</head>
<body>
<div class="card">
  <svg class="top-wave" viewBox="0 0 1200 90" preserveAspectRatio="none" aria-hidden="true">
    <path d="M0 0 H1200 V53 Q600 112 0 53 Z" fill="var(--magenta)"/>
  </svg>

  <div class="brand">
    <div class="brand-dot" aria-hidden="true"></div>
    <div class="brand-name">Maplebrook Pediatric Dentistry</div>
  </div>

  <div class="stripe stripe--upper"></div>

  <section class="contact-band">
    <h1 class="doctor">MEI-RAN TSAI, DMD</h1>

    <div class="contact-row contact-row--first">
      <div class="contact-item">
        <svg class="contact-icon" viewBox="0 0 30 30" aria-hidden="true">
          <circle cx="15" cy="15" r="13.5" fill="none" stroke="#fff" stroke-width="2"/>
          <path d="M10 8.5c1-.8 2-.6 2.5.4l1 2.2c.3.7 0 1.3-.6 1.7l-.8.5c.6 1.8 1.9 3.3 3.6 4.3l.6-.8c.4-.6 1.1-.8 1.7-.4l2.1 1.2c.9.5 1 1.6.2 2.4-1.2 1.2-2.6 1.3-4.3.5-3.4-1.7-5.8-4.6-6.6-8.2-.3-1.6.1-2.9.6-3.8z" fill="#fff"/>
        </svg>
        <span>555.555.0193</span>
      </div>
      <div class="contact-item">
        <svg class="contact-icon" viewBox="0 0 30 30" aria-hidden="true">
          <circle cx="15" cy="15" r="13.5" fill="none" stroke="#fff" stroke-width="2"/>
          <rect x="8" y="10" width="14" height="10" rx="1" fill="#fff"/>
          <path d="M8.5 10.5 L15 15.5 L21.5 10.5" fill="none" stroke="var(--gold)" stroke-width="1.3"/>
        </svg>
        <span>info@maplebrook.example</span>
      </div>
    </div>

    <div class="contact-row contact-row--second">
      <div class="contact-item">
        <svg class="contact-icon" viewBox="0 0 30 30" aria-hidden="true">
          <circle cx="15" cy="15" r="13.5" fill="none" stroke="#fff" stroke-width="2"/>
          <circle cx="15" cy="15" r="7.5" fill="none" stroke="#fff" stroke-width="1.6"/>
          <ellipse cx="15" cy="15" rx="3.2" ry="7.5" fill="none" stroke="#fff" stroke-width="1.4"/>
          <path d="M7.5 15 H22.5" stroke="#fff" stroke-width="1.4"/>
        </svg>
        <span>www.maplebrookkidsdental.example</span>
      </div>
    </div>
  </section>

  <div class="stripe stripe--lower"></div>

  <section class="address-band">
    <svg class="ribbon" viewBox="0 0 610 76" preserveAspectRatio="none" aria-hidden="true">
      <path d="M0 0 H610 L565 38 L610 76 H0 Z" fill="var(--ribbon)"/>
    </svg>
    <div class="ribbon-text">
      <span class="practice">MAPLEBROOK PEDIATRIC DENTISTRY</span>
      <span class="address">482 Quarry Lane Suite 517 Alderwick, ST 00000</span>
    </div>
  </section>

  <div class="bottom-band"><div class="bottom-band-inner"></div></div>
</div>
</body>
</html>
```